Natural Light/Organic/Documentary Photography Business

I like a simple, approachable, feminine, earthy/organic feel. Earth/neutral tones, nothing too loud or obnoxious. I like the watercolor look. I don't want anything too trendy or something I'll get tired of after a couple months. As far as colors, I am much more a fan of cream/taupe/blue/green...not a fan of pink or purple at all.

Target Market(s)

Weddings & Families

Industry/Entity Type

Wedding Photography

Contact Information for Business Card

website, email, phone number

Font styles to use
Other font styles liked:
• Horizontes, Gotham

Colors

Designer to choose colors to be used in the design.

Requirements
Must have
• Website: www.mirelhatchway.com
• Phone: 418.629.5073
• Email: mirel@mirelhatchway.com
Nice to have
• I like the watercolor look but its not necessary. I like simple/earthy tones. Nothing too loud or distracting. Simple & feminine without being too girly. I like an approachable/soft feel.
• Instagram: www.instagram.com/mirelhatchwayphotography/
Should not have
• NO loud colors or design or pattern. I do not want a photo of a camera or lens or anything cheesy like that.

```html
<!DOCTYPE html>
<html lang="en">
<head>
<meta charset="UTF-8">
<title>Mirel Hatchway Photography – Business Card</title>
<link rel="stylesheet" href="https://fonts.googleapis.com/css2?family=Cormorant+Garamond:wght@300&family=Cormorant+SC:wght@500&family=Montserrat:wght@300&display=swap">
<style>
  :root {
    --card-cream: #faf2e8;
    --wash-peach: #f3dcc3;
    --wash-sand: #e6d4bf;
    --wash-taupe: #c9bcad;
    --ink-taupe: #857c77;
    --ink-dark: #4a4441;
  }
  html, body {
    margin: 0;
    padding: 0;
    overflow: hidden;
    background: var(--card-cream);
  }
  .business-card {
    position: relative;
    width: 1200px;
    height: 678px;
    background: var(--card-cream);
    overflow: hidden;
  }
  .watercolor-wash {
    position: absolute;
    left: 130px;
    top: 80px;
    width: 960px;
    height: 515px;
    border-radius: 48% 52% 45% 55% / 50% 45% 55% 50%;
    background:
      radial-gradient(ellipse 40% 35% at 30% 45%, rgba(201,188,173,0.55), transparent 70%),
      radial-gradient(ellipse 35% 30% at 80% 70%, rgba(201,188,173,0.45), transparent 70%),
      radial-gradient(ellipse 45% 40% at 55% 35%, rgba(243,220,195,0.85), transparent 75%),
      radial-gradient(ellipse 50% 50% at 50% 50%, var(--wash-sand), transparent 80%);
    filter: blur(14px);
    opacity: 0.9;
  }
  .brand {
    position: absolute;
    left: 0;
    right: 0;
    top: 240px;
    text-align: center;
  }
  .brand-name {
    margin: 0;
    font-family: "Cormorant Garamond", serif;
    font-weight: 300;
    font-size: 98px;
    line-height: 1;
    color: var(--ink-taupe);
    letter-spacing: 2px;
  }
  .brand-tagline {
    margin: 18px 0 0 40px;
    font-family: "Montserrat", sans-serif;
    font-weight: 300;
    font-size: 18px;
    letter-spacing: 9px;
    color: var(--ink-taupe);
  }
  .contact-line {
    position: absolute;
    left: 0;
    right: 0;
    top: 624px;
    text-align: center;
    font-family: "Cormorant SC", serif;
    font-weight: 500;
    font-size: 17px;
    color: var(--ink-dark);
    white-space: nowrap;
  }
</style>
</head>
<body>
  <main class="business-card">
    <div class="watercolor-wash" role="img" aria-label="Soft watercolor wash in cream, peach and taupe tones"></div>
    <header class="brand">
      <h1 class="brand-name">Mirel Hatchway</h1>
      <p class="brand-tagline">PHOTOGRAPHY</p>
    </header>
    <footer class="contact-line">
      Cell: 418.629.5073| Email: mirel@mirelhatchway.com |Web: www. mirelhatchway.com | Insta: @mirelhatchwayphotography
    </footer>
  </main>
</body>
</html>
```